Ridgeway Mining Solutions Business Card

Ridgeway Mining Solutions is a company that provides consulting services to the Mining Industry.

Whilst Ridgeway Mining Solutions is an Australian based company its client base is the global mining industry.

The essence of Ridgeway Mining Solutions is its a can do organisation that can make a difference to its clients by providing quality assistance and form lasting relationships.
Updates

Target Market(s)

The global Mining Industry.

Industry/Entity Type

Mining

Font styles to use
Serif

Colors

Designer to choose colors to be used in the design.

Requirements
Nice to have
• My thinking is the card would look good in black given the logo.

I would like to see written on the back side of the card " Providing Metallurgical, Management and Corporate Services to the Mining Industry"

```html
<!DOCTYPE html>
<html lang="en">
<head>
<meta charset="utf-8">
<title>Ridgeway Mining Solutions – Business Card</title>
<link rel="stylesheet" href="https://fonts.googleapis.com/css2?family=Tinos:wght@400;700&display=swap">
<style>
  :root {
    --page-bg: #f4f4f4;
    --card-bg: #0b0b0b;
    --accent: #f5a41f;
    --text-light: #ffffff;
    --text-dark: #111111;
    --hairline: #2a2a2a;
    --shadow: rgba(0, 0, 0, 0.45);
  }
  * { margin: 0; padding: 0; box-sizing: border-box; }
  html, body {
    width: 992px; height: 1200px; overflow: hidden;
    background: var(--page-bg);
    font-family: "Tinos", "Times New Roman", serif;
  }
  .sheet { position: relative; width: 992px; height: 1200px; }

  .card {
    position: absolute; left: 67px;
    width: 863px; height: 491px;
    background: var(--card-bg);
    border-radius: 46px;
    box-shadow: 6px 8px 10px var(--shadow);
    overflow: hidden;
  }
  .card--front { top: 66px; }
  .card--back  { top: 620px; }

  .hairline { position: absolute; height: 1px; background: var(--hairline); }
  .accent-rule { position: absolute; left: 0; right: 0; height: 2px; background: var(--accent); }

  .brand-name {
    position: absolute;
    color: var(--accent);
    font-weight: 700;
    text-transform: uppercase;
    line-height: 1;
    text-align: center;
  }
  .brand-name__main { display: block; }
  .brand-name__sub { display: block; }

  .card--front .hairline { top: 95px; left: 253px; width: 365px; }
  .card--front .brand-name { left: 0; right: 0; top: 182px; }
  .card--front .brand-name__main { font-size: 74px; letter-spacing: 2px; }
  .card--front .brand-name__sub { font-size: 25px; letter-spacing: 6px; margin-top: 10px; }
  .card--front .accent-rule { top: 355px; }
  .tagline {
    position: absolute; left: 0; right: 0; top: 369px;
    text-align: center; color: var(--text-light);
    font-size: 26px; letter-spacing: 0.2px;
  }

  .card--back .hairline { top: 53px; left: 72px; width: 237px; }
  .card--back .brand-name { left: 80px; width: 224px; top: 118px; }
  .card--back .brand-name__main { font-size: 44px; letter-spacing: 1px; }
  .card--back .brand-name__sub { font-size: 15px; letter-spacing: 3px; margin-top: 6px; }

  .name-bar { position: absolute; left: 179px; top: 243px; width: 637px; height: 60px; }
  .name-bar svg { position: absolute; inset: 0; }
  .name-bar__name {
    position: absolute; left: 0; width: 270px; top: 0; height: 60px;
    display: flex; align-items: center; justify-content: center;
    color: var(--text-dark); font-size: 26px;
  }
  .name-bar__title {
    position: absolute; left: 275px; right: 0; top: 0; height: 60px;
    display: flex; align-items: center; justify-content: center;
    color: var(--text-dark); font-size: 16px;
  }

  .card--back .accent-rule { top: 355px; }
  .contact { position: absolute; color: var(--text-light); font-size: 20px; line-height: 1; }
  .contact--phone { left: 103px; top: 383px; }
  .contact--email { left: 310px; top: 378px; }
  .contact--web { left: 568px; top: 380px; }
  .contact--address { left: 103px; top: 434px; }
  .divider { position: absolute; top: 370px; width: 2px; height: 44px; background: var(--text-light); }
  .divider--one { left: 270px; }
  .divider--two { left: 531px; }
</style>
</head>
<body>
<main class="sheet">
  <section class="card card--front" aria-label="Card front">
    <div class="hairline"></div>
    <h1 class="brand-name">
      <span class="brand-name__main">Ridgeway</span>
      <span class="brand-name__sub">Mining Solutions</span>
    </h1>
    <div class="accent-rule"></div>
    <p class="tagline">We provide consulting services to the Mining Industry..</p>
  </section>

  <section class="card card--back" aria-label="Card back">
    <div class="hairline"></div>
    <h2 class="brand-name">
      <span class="brand-name__main">Ridgeway</span>
      <span class="brand-name__sub">Mining Solutions</span>
    </h2>

    <div class="name-bar">
      <svg width="637" height="60" viewBox="0 0 637 60" aria-hidden="true">
        <path d="M6 0 H271 L258 60 H6 Q0 60 0 54 V6 Q0 0 6 0 Z" fill="var(--accent)"/>
        <path d="M281 0 H631 Q637 0 637 6 V54 Q637 60 631 60 H268 Z" fill="var(--accent)"/>
      </svg>
      <span class="name-bar__name">Daniel Hartley</span>
      <span class="name-bar__title">Managing Director</span>
    </div>

    <div class="accent-rule"></div>
    <span class="contact contact--phone">0061 2458 731</span>
    <span class="divider divider--one"></span>
    <span class="contact contact--email">info@ridgewaymining.com</span>
    <span class="divider divider--two"></span>
    <span class="contact contact--web">www.ridgewaymining.com</span>
    <span class="contact contact--address">Ridgeway Consulting Pty 14 Ore St, Perth WA 6000</span>
  </section>
</main>
</body>
</html>
```